RB Halden Electric Yard Sign

Looking to have a yard sign designed that we can place at projects we are working on. Most likely will be 18" H x 24" W but flexible that we can increase the size if necessary. It should include our logo, our phone # 609-555-0147, website rbhaldenelectric.example and slogan, built on integrity, driven by excellence. Colors should match our brand.

```html
<!DOCTYPE html>
<html lang="en">
<head>
<meta charset="utf-8">
<title>RB Halden Electric Yard Sign</title>
<link rel="stylesheet" href="https://fonts.googleapis.com/css2?family=Montserrat:wght@600;700;800&display=swap">
<style>
  :root {
    --navy: #04356b;
    --red: #e31e26;
    --white: #ffffff;
    --backdrop: #eef0f2;
  }
  * { margin: 0; padding: 0; box-sizing: border-box; }
  html, body {
    width: 1200px;
    height: 1200px;
    overflow: hidden;
    background: var(--backdrop);
    font-family: "Montserrat", sans-serif;
  }
  .yard-sign {
    position: absolute;
    left: 40px;
    top: 180px;
    width: 1120px;
    height: 840px;
    background: var(--navy);
  }
  .sign-frame {
    position: absolute;
    inset: 0;
  }
  .brand-dot {
    position: absolute;
    left: 500px;
    top: 110px;
    width: 120px;
    height: 120px;
    border-radius: 50%;
    background: var(--red);
  }
  .brand-name {
    position: absolute;
    left: 0;
    right: 0;
    top: 248px;
    text-align: center;
    font-weight: 800;
    font-size: 90px;
    line-height: 1;
    letter-spacing: 4px;
    color: var(--red);
    text-transform: uppercase;
  }
  .trade-line {
    position: absolute;
    left: 0;
    right: 0;
    top: 352px;
    text-align: center;
    font-weight: 800;
    font-size: 46px;
    line-height: 1;
    letter-spacing: 13px;
    color: var(--white);
    padding-left: 13px;
  }
  .slogan {
    position: absolute;
    left: 0;
    right: 0;
    top: 454px;
    text-align: center;
    font-weight: 800;
    font-size: 68px;
    line-height: 72px;
    color: var(--white);
    text-transform: uppercase;
  }
  .phone {
    position: absolute;
    left: 0;
    right: 0;
    top: 630px;
    text-align: center;
    font-weight: 800;
    font-size: 122px;
    line-height: 1;
    color: var(--red);
    letter-spacing: -1px;
  }
  .website {
    position: absolute;
    left: 0;
    right: 0;
    top: 758px;
    text-align: center;
    font-weight: 700;
    font-size: 44px;
    line-height: 1;
    color: var(--white);
  }
</style>
</head>
<body>
  <div class="yard-sign">
    <svg class="sign-frame" width="1120" height="840" viewBox="0 0 1120 840" aria-hidden="true">
      <defs>
        <linearGradient id="divider-fade" x1="0" x2="1" y1="0" y2="0">
          <stop offset="0" stop-color="#e31e26" stop-opacity="0"/>
          <stop offset="0.5" stop-color="#e31e26" stop-opacity="1"/>
          <stop offset="1" stop-color="#e31e26" stop-opacity="0"/>
        </linearGradient>
        <polygon id="star" points="0,-16 4.7,-5.2 16,-4.9 7.2,2.4 10,14 0,7.4 -10,14 -7.2,2.4 -16,-4.9 -4.7,-5.2"/>
      </defs>
      <!-- frame with gaps for stars and web address -->
      <polyline points="440,52 50,52 50,788 264,788" fill="none" stroke="#e31e26" stroke-width="7"/>
      <polyline points="682,52 1071,52 1071,788 857,788" fill="none" stroke="#e31e26" stroke-width="7"/>
      <!-- rating stars -->
      <g fill="#ffffff">
        <use href="#star" x="470" y="54"/>
        <use href="#star" x="515" y="54"/>
        <use href="#star" x="561" y="54"/>
        <use href="#star" x="607" y="54"/>
        <use href="#star" x="652" y="54"/>
      </g>
      <!-- underline beneath trade line -->
      <polygon points="108,402 1012,402 995,410 125,410" fill="#e31e26"/>
      <rect x="126" y="411" width="868" height="3" fill="#ffffff"/>
      <!-- slogan divider -->
      <rect x="244" y="609" width="634" height="4" fill="url(#divider-fade)"/>
    </svg>

    <div class="brand-dot"></div>
    <div class="brand-name">R.B. Halden</div>
    <div class="trade-line">Electrical Contractor</div>
    <p class="slogan">Built on integrity,<br>driven by excellence</p>
    <div class="phone">609-555-0147</div>
    <div class="website">rbhaldenelectric.example</div>
  </div>
</body>
</html>
```